Modern Business Card

Modern professional business card with more than just logo and demographic info. Something memorable.

We are a trendy/modern chiropractic group with an emphasis on neurology, hence the minimalist-type brain logo. We want to convey that modern and technical aspect with professionalism and the elite nature of our practice environment.

```html
<!DOCTYPE html>
<html lang="en">
<head>
<meta charset="utf-8">
<title>Meridian Spine Group – Business Card</title>
<link href="https://fonts.googleapis.com/css2?family=Open+Sans:wght@400;600;700&display=swap" rel="stylesheet">
<style>
  :root {
    --stage: #e6e6e4;
    --card-white: #ffffff;
    --card-dark: #2b2b2d;
    --brand-blue: #3f7cc8;
    --ink: #2a2a2a;
    --ink-soft: #4a4a4a;
    --emboss: #1a1a1b;
  }
  * { box-sizing: border-box; margin: 0; padding: 0; }
  html, body {
    width: 1200px; height: 900px; overflow: hidden;
    background: var(--stage);
    font-family: "Open Sans", Arial, sans-serif;
  }
  .stage {
    width: 1200px; height: 900px;
    display: flex; flex-direction: column;
    align-items: center; justify-content: center; gap: 40px;
  }
  .card {
    position: relative;
    width: 700px; height: 400px;
    overflow: hidden;
    box-shadow: 0 8px 24px rgba(0,0,0,0.18);
  }

  /* Wordmark */
  .wordmark {
    display: flex; align-items: center; gap: 14px;
    font-weight: 600; letter-spacing: 0.05em; text-transform: uppercase;
    font-size: 28px; line-height: 1.1;
  }
  .wordmark-mark { width: 26px; height: 26px; flex: none; }

  /* Back face */
  .card-back {
    background: var(--card-dark);
    display: flex; align-items: center; justify-content: center;
  }
  .card-back .wordmark { color: var(--emboss); font-size: 32px; }
  .card-back .wordmark-mark { background: var(--emboss); width: 30px; height: 30px; }

  /* Front face */
  .card-front { background: var(--card-white); }
  .front-swoosh { position: absolute; inset: 0; width: 700px; height: 400px; }
  .front-swoosh .swoosh-blue { fill: var(--brand-blue); }
  .front-swoosh .swoosh-gap { fill: var(--card-white); }
  .front-swoosh .swoosh-dark { fill: var(--card-dark); }

  .card-front .wordmark {
    position: absolute; left: 110px; top: 176px;
    color: var(--ink);
  }
  .card-front .wordmark-mark { background: var(--brand-blue); }

  .contact {
    position: absolute; left: 440px; top: 64px;
    padding-left: 16px;
    border-left: 1.5px solid var(--brand-blue);
    color: var(--ink-soft);
    font-size: 13px; line-height: 1.45;
  }
  .contact-name {
    color: var(--brand-blue); font-weight: 700;
    font-size: 19px; letter-spacing: 0.01em; line-height: 1.2;
  }
  .contact-role { margin-bottom: 8px; }
  .contact-lines { margin-bottom: 10px; }
  .contact-row { display: flex; align-items: center; gap: 6px; }
  .contact-row svg { width: 11px; height: 11px; fill: var(--brand-blue); flex: none; }

  .website {
    position: absolute; left: 46px; bottom: 14px;
    color: #ffffff; font-size: 13px; letter-spacing: 0.02em;
    transform: rotate(-12deg); transform-origin: left bottom;
  }
</style>
</head>
<body>
<main class="stage">

  <section class="card card-back" aria-label="Card back">
    <div class="wordmark"><span class="wordmark-mark"></span><span>Meridian<br>Spine Group</span></div>
  </section>

  <section class="card card-front" aria-label="Card front">
    <svg class="front-swoosh" viewBox="0 0 700 400" aria-hidden="true">
      <path class="swoosh-blue" d="M0,378 C70,316 180,290 320,282 C470,274 610,272 700,232 L700,400 L0,400 Z"/>
      <path class="swoosh-gap" d="M0,386 C70,324 180,298 320,290 C470,282 610,280 700,240 L700,400 L0,400 Z"/>
      <path class="swoosh-dark" d="M0,400 L0,392 C70,330 180,304 320,296 C470,288 610,286 700,246 L700,400 Z"/>
    </svg>

    <div class="wordmark"><span class="wordmark-mark"></span><span>Meridian<br>Spine Group</span></div>

    <div class="contact">
      <p class="contact-name">EVAN HOLLOWAY</p>
      <p class="contact-role">President</p>
      <p class="contact-lines">1180 Harbor Crest Way<br>Seacliff CA 92700</p>
      <p class="contact-row">
        <svg viewBox="0 0 24 24"><path d="M6.6 10.8a15.1 15.1 0 0 0 6.6 6.6l2.2-2.2c.3-.3.7-.4 1-.2 1.1.4 2.3.6 3.6.6.6 0 1 .4 1 1V20c0 .6-.4 1-1 1A17 17 0 0 1 3 4c0-.6.4-1 1-1h3.5c.6 0 1 .4 1 1 0 1.3.2 2.5.6 3.6.1.3 0 .7-.2 1z"/></svg>
        555-014-2286
      </p>
      <p class="contact-row">
        <svg viewBox="0 0 24 24"><path d="M2 5h20v14H2z M2 5l10 8 10-8"/></svg>
        evan@meridianspinegroup.com
      </p>
    </div>

    <p class="website">meridianspinegroup.com</p>
  </section>

</main>
</body>
</html>
```